Dietitian needs awesome business card

I need a contemporary design that's eye catching but professional.
My card is to given to doctors, specialists and patients alike.
I manage patients with chronic diseases
I have uploaded my logo and current business card, I would also like the other Certified Clinical Nutritionist logo incorporated into the design

Target Market(s)

Doctors, specialists and patients

Industry/Entity Type

Healthcare

Contact Information for Business Card

www.brightfieldnutrition.com.au
Ph: 0427 561 903
Fax: 6457 2183
email: marcus.k.diet@fernmail.com
Space on the back of the card with: Appointment date, Appointment time and appointment location

Font styles to use
Serif

Colors
fbee3e
876aae
ffc214

Requirements
Must have
• My Logo
• Certified Clinical Nutritionist Logo
• My 4 locations - Pinebrook Medical Centre, North Corrin Health, Hollis Medical, Ashcombe Doctors Surgery
Nice to have
• I like the colours in my current business card

```html
<!DOCTYPE html>
<html lang="en">
<head>
<meta charset="utf-8">
<title>Brightfield Nutrition & Dietetics – Business Card</title>
<link rel="stylesheet" href="https://fonts.googleapis.com/css2?family=Philosopher:wght@400;700&family=Source+Sans+3:wght@400;600&display=swap">
<style>
  :root {
    --page-bg: #e6e6e6;
    --card-bg: #ffffff;
    --brand-blue: #1f3f98;
    --brand-green: #8cc63f;
    --text-grey: #555a60;
    --rule-grey: #b9bcc0;
    --badge-orange: #f07b22;
    --shadow: rgba(0, 0, 0, 0.18);
  }
  * { margin: 0; padding: 0; box-sizing: border-box; }
  html, body {
    width: 1105px; height: 1200px; overflow: hidden;
    background: var(--page-bg);
    font-family: "Source Sans 3", "Helvetica Neue", Arial, sans-serif;
    color: var(--text-grey);
  }
  .card {
    position: absolute; left: 102px;
    width: 900px; height: 515px;
    background: var(--card-bg);
    box-shadow: 0 6px 18px var(--shadow);
  }
  .card--front { top: 50px; }
  .card--back { top: 635px; }

  /* front */
  .holder-name {
    position: absolute; left: 52px; top: 236px;
    font-family: "Philosopher", Georgia, serif;
    font-size: 34px; color: var(--brand-blue);
  }
  .holder-role {
    position: absolute; left: 52px; top: 282px;
    font-family: "Philosopher", Georgia, serif;
    font-size: 25px; color: var(--brand-green);
  }
  .contact-list { position: absolute; left: 52px; top: 335px; list-style: none; }
  .contact-list li {
    display: flex; align-items: center; gap: 12px;
    height: 34px; font-size: 23px; color: var(--text-grey);
  }
  .contact-list svg { width: 20px; height: 20px; fill: var(--brand-blue); flex: none; }

  .front-mark {
    position: absolute; left: 462px; top: 80px;
    width: 440px; height: 380px;
  }
  .front-mark__circle {
    position: absolute; left: 30px; top: 0;
    width: 380px; height: 380px; border-radius: 50%;
    background: var(--brand-green);
  }
  .front-mark__name {
    position: absolute; left: 0; right: 0; top: 166px; text-align: center;
    font-family: "Philosopher", Georgia, serif;
    font-size: 42px; color: #ffffff;
  }

  /* back */
  .practice-mark {
    position: absolute; left: 58px; top: 60px;
    display: flex; align-items: center; gap: 14px;
  }
  .practice-mark__dot {
    width: 64px; height: 64px; border-radius: 50%; background: var(--brand-green);
  }
  .practice-mark__name {
    font-family: "Philosopher", Georgia, serif;
    font-size: 36px; line-height: 1.05; color: var(--brand-blue);
  }
  .credential-badge {
    position: absolute; left: 608px; top: 48px;
    width: 215px; height: 100px; background: var(--badge-orange); border-radius: 3px;
  }
  .note-line {
    position: absolute; left: 60px; width: 777px; height: 0;
    border-top: 1.5px solid var(--rule-grey);
  }
  .appointment-row {
    position: absolute; top: 333px; left: 60px; width: 790px; height: 36px;
    font-family: "Philosopher", Georgia, serif; color: var(--brand-blue);
  }
  .appointment-row .label { position: absolute; top: 0; font-size: 26px; }
  .appointment-row .fill-line {
    position: absolute; top: 30px; border-top: 1.5px solid var(--rule-grey);
  }
  .appointment-row .meridiem {
    position: absolute; top: 8px; left: 715px;
    font-family: "Source Sans 3", Arial, sans-serif; font-size: 19px;
  }
  .location-list { position: absolute; top: 398px; left: 60px; list-style: none; }
  .location-list li {
    position: absolute; display: flex; align-items: center; gap: 12px;
    font-size: 24px; white-space: nowrap; color: var(--text-grey);
  }
  .location-box { width: 20px; height: 20px; border: 2px solid var(--brand-blue); flex: none; }
</style>
</head>
<body>

<section class="card card--front" aria-label="Card front">
  <div class="holder-name">Marcus Kellaway</div>
  <div class="holder-role">Nutritionist &amp; Chef</div>
  <ul class="contact-list">
    <li><svg viewBox="0 0 24 24" aria-hidden="true"><path d="M6.6 10.8a15.1 15.1 0 0 0 6.6 6.6l2.2-2.2c.3-.3.7-.4 1-.2 1.1.4 2.3.6 3.6.6.6 0 1 .4 1 1V20c0 .6-.4 1-1 1C10.6 21 3 13.4 3 4c0-.6.4-1 1-1h3.5c.6 0 1 .4 1 1 0 1.3.2 2.5.6 3.6.1.3 0 .7-.2 1z"/></svg>0427 561 903</li>
    <li><svg viewBox="0 0 24 24" aria-hidden="true"><path d="M7 3h10v5H7zM4 9h16a2 2 0 0 1 2 2v6h-4v4H6v-4H2v-6a2 2 0 0 1 2-2zm4 7v3h8v-3z"/></svg>6457 2183</li>
    <li><svg viewBox="0 0 24 24" aria-hidden="true"><path d="M2 5h20v14H2zm2 2v.5l8 5 8-5V7zm0 2.8V17h16V9.8l-8 5z"/></svg>marcus.k.diet@fernmail.com</li>
    <li><svg viewBox="0 0 24 24" aria-hidden="true"><path d="M12 2a10 10 0 1 0 0 20 10 10 0 0 0 0-20zm6.9 9h-3a15 15 0 0 0-1.3-5.9A8 8 0 0 1 18.9 11zM12 4c.9 1.2 1.8 3.8 1.9 7h-3.8c.1-3.2 1-5.8 1.9-7zM9.4 5.1A15 15 0 0 0 8.1 11h-3a8 8 0 0 1 4.3-5.9zM5.1 13h3a15 15 0 0 0 1.3 5.9A8 8 0 0 1 5.1 13zM12 20c-.9-1.2-1.8-3.8-1.9-7h3.8c-.1 3.2-1 5.8-1.9 7zm2.6-1.1a15 15 0 0 0 1.3-5.9h3a8 8 0 0 1-4.3 5.9z"/></svg>brightfieldnutrition.com.au</li>
  </ul>
  <div class="front-mark">
    <div class="front-mark__circle"></div>
    <div class="front-mark__name">Brightfield</div>
  </div>
</section>

<section class="card card--back" aria-label="Card back">
  <div class="practice-mark">
    <div class="practice-mark__dot"></div>
    <div class="practice-mark__name">Brightfield<br>Nutrition &amp; Dietetics</div>
  </div>
  <div class="credential-badge" role="img" aria-label="Certified Clinical Nutritionist badge"></div>

  <div class="note-line" style="top:200px"></div>
  <div class="note-line" style="top:248px"></div>
  <div class="note-line" style="top:298px"></div>

  <div class="appointment-row">
    <span class="label" style="left:0">Date :</span>
    <span class="fill-line" style="left:78px;width:367px"></span>
    <span class="label" style="left:455px">Time :</span>
    <span class="fill-line" style="left:533px;width:174px"></span>
    <span class="meridiem">AM/PM</span>
  </div>

  <ul class="location-list">
    <li style="left:0;top:0"><span class="location-box"></span>Pinebrook Medical Centre</li>
    <li style="left:0;top:37px"><span class="location-box"></span>North Corrin Health</li>
    <li style="left:453px;top:0"><span class="location-box"></span>Ashcombe Doctors Surgery</li>
    <li style="left:453px;top:37px"><span class="location-box"></span>Hollis Medical</li>
  </ul>
</section>

</body>
</html>
```